A clean crisp business card for a Landscape Construction company. Designed to be easy to read contact/ info and also be appealing/interesting, unlike a traditional business card.

Industry/Entity Type

Landscape Construction

Contact Information for Business Card

Company name : Brambleford Landscape Construction, phone number: (877) 62Vista, website:Bramblefordyards.example, Email, sales@bramblefordyards.example

Requirements
Nice to have
• Luxurious finishes/ details…. Icons or emblems next to contact info
Should not have
• Clipart or general pictures

```html
<!DOCTYPE html>
<html lang="en">
<head>
<meta charset="utf-8">
<title>Brambleford Landscape Construction – Business Card</title>
<link rel="stylesheet" href="https://fonts.googleapis.com/css2?family=Oswald:wght@500&family=Jost:wght@400;500&display=swap">
<style>
  :root {
    --backdrop: #9a9a9a;
    --card: #262626;
    --frame-blue: #2f7fd3;
    --leaf-green: #8cc63f;
    --text-white: #f2f2f2;
    --rule-grey: #bdbdbd;
    --silver: #c9c9c9;
  }
  html, body {
    margin: 0;
    padding: 0;
    overflow: hidden;
  }
  .canvas {
    position: relative;
    width: 1200px;
    height: 1078px;
    background: var(--backdrop);
    overflow: hidden;
  }
  .card {
    position: absolute;
    background: var(--card);
    box-shadow: 0 8px 22px rgba(0,0,0,0.28);
  }

  /* Front: contact side, portrait */
  .card-front {
    left: 90px;
    top: 229px;
    width: 360px;
    height: 620px;
  }
  .card-front .frame {
    position: absolute;
    inset: 16px;
    border: 4px solid var(--frame-blue);
  }
  .card-front .content {
    position: absolute;
    left: 0;
    right: 0;
    top: 150px;
    display: flex;
    flex-direction: column;
    align-items: center;
    text-align: center;
  }
  .emblem {
    width: 34px;
    height: 34px;
    border-radius: 50%;
    background: var(--leaf-green);
    margin-bottom: 22px;
  }
  .person-name {
    font-family: "Oswald", sans-serif;
    font-weight: 500;
    font-size: 34px;
    letter-spacing: 0.5px;
    line-height: 1;
    margin: 0;
  }
  .person-name .first { color: var(--frame-blue); }
  .person-name .last { color: var(--leaf-green); }
  .person-title {
    font-family: "Jost", sans-serif;
    font-size: 17px;
    color: var(--text-white);
    margin: 8px 0 0;
  }
  .rule {
    width: 200px;
    height: 1px;
    background: var(--rule-grey);
    margin: 22px 0 20px;
  }
  .contact-list {
    list-style: none;
    margin: 0;
    padding: 0;
    display: flex;
    flex-direction: column;
    gap: 10px;
  }
  .contact-item {
    display: flex;
    align-items: center;
    gap: 10px;
    font-family: "Jost", sans-serif;
    font-size: 16px;
    color: var(--text-white);
  }
  .contact-icon {
    width: 20px;
    height: 20px;
    flex: none;
  }

  /* Back: company side, landscape */
  .card-back {
    left: 500px;
    top: 359px;
    width: 620px;
    height: 360px;
    display: flex;
    align-items: center;
    justify-content: center;
  }
  .company-lockup {
    display: flex;
    align-items: center;
    gap: 16px;
  }
  .company-dot {
    width: 22px;
    height: 22px;
    border-radius: 50%;
    background: var(--silver);
    flex: none;
  }
  .company-name {
    font-family: "Jost", sans-serif;
    font-weight: 500;
    font-size: 26px;
    letter-spacing: 1px;
    color: var(--silver);
    margin: 0;
  }
</style>
</head>
<body>
<div class="canvas">

  <section class="card card-front" aria-label="Business card contact side">
    <div class="frame"></div>
    <div class="content">
      <div class="emblem" aria-hidden="true"></div>
      <h1 class="person-name"><span class="first">DANIEL</span> <span class="last">HARLOW</span></h1>
      <p class="person-title">President</p>
      <div class="rule"></div>
      <ul class="contact-list">
        <li class="contact-item">
          <svg class="contact-icon" viewBox="0 0 20 20" aria-hidden="true">
            <circle cx="10" cy="10" r="10" fill="#2f7fd3"/>
            <path d="M7 5.5 L8.6 5.5 L9.3 8 L8.2 9 Q9 11 11 11.8 L12 10.7 L14.5 11.4 L14.5 13 Q14 14.5 12.5 14.3 Q6 13 5.7 7.5 Q5.6 5.8 7 5.5 Z" fill="#fff"/>
          </svg>
          (877) 62Vista
        </li>
        <li class="contact-item">
          <svg class="contact-icon" viewBox="0 0 20 20" aria-hidden="true">
            <circle cx="10" cy="10" r="10" fill="#2f7fd3"/>
            <rect x="5" y="6.5" width="10" height="7" fill="#fff"/>
            <path d="M5 6.5 L10 10.5 L15 6.5" fill="none" stroke="#2f7fd3" stroke-width="1.2"/>
          </svg>
          sales@bramblefordyards.example
        </li>
        <li class="contact-item">
          <svg class="contact-icon" viewBox="0 0 20 20" aria-hidden="true">
            <circle cx="10" cy="10" r="10" fill="#2f7fd3"/>
            <circle cx="10" cy="10" r="5" fill="none" stroke="#fff" stroke-width="1.3"/>
            <ellipse cx="10" cy="10" rx="2.2" ry="5" fill="none" stroke="#fff" stroke-width="1.1"/>
            <line x1="5" y1="10" x2="15" y2="10" stroke="#fff" stroke-width="1.1"/>
          </svg>
          Bramblefordyards.example
        </li>
      </ul>
    </div>
  </section>

  <section class="card card-back" aria-label="Business card company side">
    <div class="company-lockup">
      <div class="company-dot" aria-hidden="true"></div>
      <h2 class="company-name">Brambleford Landscape Construction</h2>
    </div>
  </section>

</div>
</body>
</html>
```